4th Generation Family Business Needs a New Card Design!

We are a family owned 4th Generation company. We are based in the Sydney, Australia area and we are desperately in need of a more modern and classy card. We are monumental masons who design, supply & erect lasting memorials throughout cemeteries in Sydney. Our customers are normally in a period of grieving. I have attached logo files that will need to be implemented on the card. Company was established 1935. Australian Owned and Operated. Card needs to be designed to PIXO.com specification.

Target Market(s)

Our target market is based upon people that a grieving for family members that have passed away. We also deal with alot of companies that own and operate cemeteries.

Industry/Entity Type

Business

Contact Information for Business Card

Simon Harcourt, Operations Manager, 0417293086, simon@harcourtmemorials.com.au
Lewis Harcourt, Director, 0491630572, lewis@harcourtmemorials.com.au
Phone # 02 9561 3048
Website: www.harcourtmemorials.com.au
Address: Suite 17, 8 Palfrey Lane, West Carlow, Sydney NSW 2156

Font styles to use
Serif
Decorative
Script

Requirements
Must have
• Would like to see the logo nicely implemented with a modern design. Embossed lettering would be a nice additive.

```html
<!DOCTYPE html>
<html lang="en">
<head>
<meta charset="utf-8">
<title>Harcourt Memorials – Business Card</title>
<link rel="stylesheet" href="https://fonts.googleapis.com/css2?family=Cinzel:wght@400;600&family=Tinos&display=swap">
<style>
  :root {
    --backdrop: #e6e6e6;
    --card-black: #0b0c0e;
    --card-sheen: #2c2d30;
    --gold: #e2b524;
    --white: #ffffff;
    --soft-white: #e9e9e9;
  }
  * { margin: 0; padding: 0; box-sizing: border-box; }
  html, body {
    width: 1200px; height: 576px; overflow: hidden;
    background: var(--backdrop);
  }
  .stage { position: relative; width: 1200px; height: 576px; }

  .card {
    position: absolute;
    top: 138px;
    height: 294px;
    overflow: hidden;
    box-shadow: 0 3px 6px rgba(0,0,0,0.35);
  }
  .card-front {
    left: 81px; width: 485px;
    background:
      linear-gradient(90deg, transparent 25%, rgba(70,72,76,0.55) 38%, rgba(40,41,44,0.3) 46%, transparent 60%),
      var(--card-black);
  }
  .card-front .gold-band {
    position: absolute; left: 0; right: 0; bottom: 0; height: 11px;
    background: linear-gradient(90deg, #d9a91c, var(--gold) 45%, #f0cf5a 55%, var(--gold) 70%, #d9a91c);
  }
  .front-brand {
    position: absolute; left: 0; right: 0; top: 118px;
    text-align: center;
    font-family: 'Cinzel', serif;
    font-weight: 400;
    color: var(--white);
    font-size: 33px;
    line-height: 1.1;
    letter-spacing: 1px;
  }

  .card-back {
    left: 602px; width: 481px; height: 292px;
    background:
      linear-gradient(90deg, transparent 22%, rgba(70,72,76,0.55) 37%, rgba(40,41,44,0.3) 46%, transparent 60%),
      var(--card-black);
  }
  .card-back .gold-strip {
    position: absolute; left: 0; top: 0; bottom: 0; width: 40px;
    background: linear-gradient(180deg, #d9a91c, var(--gold) 50%, #d9a91c);
  }
  .card-back .white-strip {
    position: absolute; left: 40px; top: 0; bottom: 0; width: 5px;
    background: var(--soft-white);
  }
  .person-name {
    position: absolute; left: 62px; top: 24px;
    font-family: 'Cinzel', serif; font-weight: 400;
    font-size: 22px; color: var(--white); letter-spacing: 0.5px;
  }
  .person-role {
    position: absolute; left: 62px; top: 52px;
    font-family: 'Tinos', serif; font-size: 12px; color: var(--soft-white);
  }
  .back-brand {
    position: absolute; left: 300px; width: 190px; top: 78px;
    text-align: center;
    font-family: 'Cinzel', serif; font-weight: 400;
    font-size: 24px; line-height: 1.1; color: var(--white);
  }
  .contact-list {
    position: absolute; left: 66px; top: 188px;
    list-style: none;
    font-family: 'Tinos', serif; font-size: 13px; color: var(--soft-white);
  }
  .contact-list li {
    display: flex; align-items: center; height: 17.7px;
  }
  .contact-list svg { width: 11px; height: 11px; margin-right: 8px; fill: var(--gold); }
  .address {
    position: absolute; left: 61px; top: 260px;
    font-family: 'Tinos', serif; font-size: 13px; color: var(--soft-white);
  }
</style>
</head>
<body>
<div class="stage">
  <section class="card card-front">
    <div class="front-brand">Harcourt<br>Memorials</div>
    <div class="gold-band"></div>
  </section>

  <section class="card card-back">
    <div class="gold-strip"></div>
    <div class="white-strip"></div>
    <h1 class="person-name">Simon Harcourt</h1>
    <p class="person-role">Operations Manager</p>
    <div class="back-brand">Harcourt<br>Memorials</div>
    <ul class="contact-list">
      <li>
        <svg viewBox="0 0 12 12" aria-hidden="true"><path d="M2.5 0.8 4.3 3.4 3.3 4.6c.6 1.6 2.1 3.1 3.7 3.7l1.2-1 2.6 1.8-.9 2.1C5.4 11 1 6.6.4 1.7z"/></svg>
        0491630572
      </li>
      <li>
        <svg viewBox="0 0 12 12" aria-hidden="true"><path d="M1 3.5C1 2 3 1.5 6 1.5S11 2 11 3.5V5H8.5V3.8h-5V5H1zM3 6h6l1.5 4.5h-9z"/></svg>
        02 9561 3048
      </li>
      <li>
        <svg viewBox="0 0 12 12" aria-hidden="true"><path d="M0.5 2.5h11v7h-11zM1.3 3.2 6 6.8l4.7-3.6z" fill-rule="evenodd"/></svg>
        lewis@harcourtmemorials.com.au
      </li>
      <li>
        <svg viewBox="0 0 12 12" aria-hidden="true"><circle cx="6" cy="6" r="5" fill="none" stroke="#e2b524" stroke-width="1.2"/><path d="M1 6h10M6 1v10" stroke="#e2b524" stroke-width="1"/><ellipse cx="6" cy="6" rx="2.3" ry="5" fill="none" stroke="#e2b524" stroke-width="1"/></svg>
        www.harcourtmemorials.com.au
      </li>
    </ul>
    <p class="address">Suite 17, 8 Palfrey Lane, West Carlow, Sydney NSW 2156</p>
  </section>
</div>
</body>
</html>
```